Suds Haven Laundromat Wordpress Design

We need a Wordpress website design for our laundromat, Suds Haven Atlanta, at www.sudshavenatlanta-example.com. We would like to have 6 pages: Home, About Us, Services, Locations, Reviews and Contact us. We will provide content for the text on each page. What we do: We are a full service laundromat that provides dry cleaning drop off, professional laundry services, wash dry fold and self service laundry to the local community. We would like to use the color scheme from our logo to convey a warm, safe, and bright business that caters to its diverse community.
Updates

I like the structure of this laundromat website: http://www.washtroveusa-example.com/ Using my logo and color scheme in the above referenced website is what. Am looking for. The photos attached to the project with the female model should be used as a primary focus and supplemented by actual photos of the equipment.

Target Market(s)

Our target market is a diverse group of people from Midtown Atlanta - LGBTQ community /Locals/Regulars that have been coming to laundromat for 30 years.

Industry/Entity Type

Laundromat

Coding

Coded - Design and coding required

Number of Pages Required

5+ page

Font styles to use
Sans Serif

Colors
0054AA
0677BA
7BADD7
CADEEF
E8F1F8

Requirements
Must have
• Feature this video on the main page: https://videohost-example.com/xq7Rm2bPz4k

```html
<!DOCTYPE html>
<html lang="en">
<head>
<meta charset="utf-8">
<title>Suds Haven Atlanta – Reviews</title>
<link href="https://fonts.googleapis.com/css2?family=Montserrat:wght@400;500;600&family=Oswald:wght@500&display=swap" rel="stylesheet">
<style>
  :root{
    --brand:#0054aa;
    --brand-mid:#0677ba;
    --brand-light:#7badd7;
    --ink:#222;
    --text:#333;
    --footer:#2e4466;
    --footer-line:#4a5f80;
    --white:#fff;
  }
  *{margin:0;padding:0;box-sizing:border-box}
  html,body{width:858px;height:1200px;overflow:hidden;background:var(--white)}
  body{position:relative;font-family:"Montserrat",sans-serif;color:var(--text)}

  .site-header{position:absolute;top:0;left:0;width:858px;height:54px;background:var(--white);z-index:3}
  .brand{position:absolute;left:74px;top:14px;display:flex;align-items:center;gap:6px;
    font-weight:600;font-size:16px;color:var(--brand)}
  .brand-dot{width:12px;height:12px;border-radius:50%;background:var(--brand-mid)}
  .main-nav{position:absolute;top:24px;left:298px;display:flex;gap:0;font-size:9.2px;color:var(--ink)}
  .main-nav a{position:absolute;white-space:nowrap;color:inherit;text-decoration:none}
  .main-nav a.active{font-weight:600}
  .main-nav a.active::after{content:"";position:absolute;left:0;right:0;top:26px;height:3px;background:var(--brand)}
  .nav-sep{position:absolute;left:736px;top:14px;width:1px;height:26px;background:var(--brand)}
  .social-mini{position:absolute;top:22px;width:9px;height:9px;border-radius:50%;background:var(--ink)}

  .hero{position:absolute;top:54px;left:0;width:858px;height:300px}
  .hero-photo{position:absolute;inset:0;background:linear-gradient(100deg,#cfd6cf 0%,#b9bfbb 30%,#9ca3a4 60%,#7e8587 100%)}
  .hero-curve{position:absolute;left:0;bottom:0}

  .breadcrumb{position:absolute;top:360px;left:117px;font-size:9px;color:var(--ink)}
  .breadcrumb .current{color:var(--brand);font-weight:600}

  .section-title{position:absolute;top:426px;left:0;width:858px;text-align:center;
    font-family:"Oswald",sans-serif;font-weight:500;font-size:22px;letter-spacing:-.2px;color:var(--ink)}
  .section-title span{color:var(--brand)}
  .title-rule{position:absolute;top:458px;left:412px;width:34px;height:2px;background:var(--brand-mid)}

  .testimonial{position:absolute;top:517px;width:199px;height:242px;background:var(--white);
    box-shadow:0 6px 14px rgba(0,0,0,.12);text-align:center}
  .quote-badge{position:absolute;left:68px;top:-31px;width:63px;height:63px;border-radius:50%;
    background:var(--brand);border:3px solid #e9e9e9;color:#7fa3d1;font-family:"Oswald",sans-serif;
    font-size:40px;line-height:70px}
  .testimonial h3{margin-top:48px;font-size:12px;font-weight:500;color:var(--brand);letter-spacing:.3px}
  .testimonial p{margin:6px 9px 0;font-size:8.6px;line-height:17.4px;color:var(--text)}

  .site-footer{position:absolute;top:823px;left:0;width:858px;height:377px;background:var(--footer);color:var(--white)}
  .footer-brand{position:absolute;top:52px;left:0;width:858px;display:flex;justify-content:center;align-items:center;gap:9px;
    font-weight:600;font-size:24px}
  .footer-brand .brand-dot{width:18px;height:18px;background:var(--white)}
  .rule{position:absolute;height:1px;background:var(--footer-line)}
  .footer-nav{position:absolute;top:170px;font-size:11px}
  .footer-nav a{position:absolute;white-space:nowrap;color:var(--white);text-decoration:none}
  .social-round{position:absolute;top:161px;width:22px;height:22px;border-radius:50%;background:var(--white)}
  .contact{position:absolute;font-size:10px;line-height:17px}
  .contact svg{position:absolute;left:-22px;top:1px}
  .delivery{position:absolute;top:228px;left:437px;font-size:10px;color:#2ea3e3}
  .delivery b{font-weight:600}
  .hours{position:absolute;top:250px;left:437px;font-size:10px;line-height:17px}
  .copyright{position:absolute;top:332px;left:0;width:858px;text-align:center;font-size:8.6px;color:#dde3ec}
  .copyright b{font-weight:600;color:var(--white)}
</style>
</head>
<body>

<header class="site-header">
  <div class="brand"><span class="brand-dot"></span>Suds Haven</div>
  <nav class="main-nav">
    <a style="left:0">HOME</a>
    <a style="left:57px">ABOUT US</a>
    <a style="left:134px">SERVICES</a>
    <a style="left:209px">LOCATION</a>
    <a class="active" style="left:292px">REVIEWS</a>
    <a style="left:364px">CONTACT US</a>
  </nav>
  <div class="nav-sep"></div>
  <span class="social-mini" style="left:749px"></span>
  <span class="social-mini" style="left:768px"></span>
</header>

<section class="hero">
  <div class="hero-photo" role="img" aria-label="Laundromat interior with rows of washers and dryers"></div>
  <svg class="hero-curve" width="858" height="70" viewBox="0 0 858 70">
    <path d="M0 60 Q420 100 858 30 L858 70 L0 70 Z" fill="#fff"/>
    <path d="M0 42 Q420 110 820 50 Q420 100 0 55 Z" fill="#0054aa"/>
  </svg>
</section>

<div class="breadcrumb">HOME / <span class="current">REVIEWS</span></div>

<h2 class="section-title">CUSTOMER <span>TESTIMONIALS</span></h2>
<div class="title-rule"></div>

<article class="testimonial" style="left:115px">
  <div class="quote-badge">”</div>
  <h3>Marla Quintero</h3>
  <p>Great drop off laundry location to have professionals do your laundry. They are quick, honor requests about how to bag it up, and are friendly and reasonable. They are also opened 7 days a week and have coin service, folding tables and a comfortable waiting area while you do your own.</p>
</article>
<article class="testimonial" style="left:330px">
  <div class="quote-badge">”</div>
  <h3>Dorian Vale</h3>
  <p>Great customer service, friendly staff, the place looks clean &amp; they have the option to pay with your phone &amp; coins, great acco- mmodating to the customers. Thank you!</p>
</article>
<article class="testimonial" style="left:544px">
  <div class="quote-badge">”</div>
  <h3>Terrell Okafor</h3>
  <p>This is one of the cleanest and friendly Coin Laundromats I've ever been too. Great place!</p>
</article>

<footer class="site-footer">
  <div class="footer-brand"><span class="brand-dot"></span>Suds Haven</div>
  <div class="rule" style="top:142px;left:214px;width:430px"></div>
  <nav class="footer-nav">
    <a style="left:182px">Home</a>
    <a style="left:242px">About Us</a>
    <a style="left:319px">Services</a>
    <a style="left:392px">Location</a>
    <a style="left:471px">Reviews</a>
    <a style="left:545px">Contact Us</a>
  </nav>
  <span class="social-round" style="left:628px"></span>
  <span class="social-round" style="left:660px"></span>
  <div class="rule" style="top:201px;left:214px;width:430px"></div>

  <div class="contact" style="top:220px;left:198px">
    <svg width="13" height="13" viewBox="0 0 14 14" fill="none" stroke="#fff" stroke-width="1"><circle cx="7" cy="7" r="6"/><path d="M1 7h12M7 1c-3 3-3 9 0 12M7 1c3 3 3 9 0 12"/></svg>
    Birchwood Plaza Shopping Center, 2210 Alder<br>Ave NE., # 118, Atlanta, GA 30399
  </div>
  <div class="contact" style="top:258px;left:197px">
    <svg width="13" height="13" viewBox="0 0 14 14" fill="none" stroke="#fff" stroke-width="1"><path d="M2 1l3 0 1 3-2 1.5c1 2 2.5 3.5 4.5 4.5L10 8l3 1v3c-6 1-12-5-11-11z"/></svg>
    (404) 555-0142
  </div>
  <div class="delivery"><b>Delivery Available*</b> please contact us for details</div>
  <div class="hours">Covid 19 hours - open 7 days a week 8 am to 8 pm<br>Last wash begins 6:30 pm</div>
  <div class="rule" style="top:297px;left:115px;width:628px"></div>
  <div class="copyright">Copyright © 2021 <b>Suds Haven Atlanta</b>. All Rights Reserved.</div>
</footer>

</body>
</html>
```